Varnex Consulting Business card design.

See our website www.varnexconsulting.example which will give you a good idea of what we are about. The font is called 'Play'.

I'd like a standout business card in keeping with the themes and branding on the website

Target Market(s)

professionals. HR directors

Industry/Entity Type

Business

Contact Information for Business Card

Varnex Consulting PO Box 3172 Merrowdale NSW 2291 1300 485 193 Gavin Threlkeld Principal email: career@varnexconsulting.example ABN: 71203948865

Font styles to use
Other font styles liked:
• Play

Requirements
Must have
• Must have same design colours and branding as website.
• On back I'd prefer a list of the things we do which appears below the name at the header on the website

```html
<!DOCTYPE html>
<html lang="en">
<head>
<meta charset="utf-8">
<title>Varnex Consulting – Business Card</title>
<link href="https://fonts.googleapis.com/css2?family=Play:wght@400;700&display=swap" rel="stylesheet">
<style>
  :root {
    --navy: #0a1f31;
    --sky: #1e97e6;
    --white: #ffffff;
    --ink: #0b1520;
    --page: #e9ebee;
    --band: rgba(10, 36, 66, 0.82);
    --tag-faint: #1f5a8e;
  }
  * { margin: 0; padding: 0; box-sizing: border-box; }
  html, body {
    width: 1189px; height: 1200px; overflow: hidden;
    background: var(--page);
    font-family: 'Play', sans-serif;
  }
  .card {
    position: absolute; left: 136px;
    width: 917px; height: 524px;
    overflow: hidden;
    box-shadow: 0 4px 14px rgba(0,0,0,0.25);
  }
  .card--front { top: 45px; background: var(--navy); }
  .card--back { top: 601px; }

  .wordmark {
    position: absolute; left: 0; right: 0;
    text-align: center; font-size: 62px; line-height: 1;
    letter-spacing: 1px; color: var(--white);
  }
  .wordmark .accent { color: var(--sky); }
  .services {
    position: absolute; left: 0; right: 0; text-align: center;
    font-size: 17px; letter-spacing: 2.6px; color: var(--sky);
    white-space: nowrap;
  }
  .services .sep { padding: 0 6px; }

  .card--front .wordmark { top: 80px; }
  .card--front .services { top: 167px; }
  .front-curve { position: absolute; left: 0; top: 0; width: 917px; height: 524px; }

  .holder {
    position: absolute; left: 20px; width: 340px; top: 360px;
    text-align: center; color: var(--ink); font-size: 30px; line-height: 38px;
  }
  .divider {
    position: absolute; left: 366px; top: 317px; width: 2px; height: 168px;
    background: var(--ink);
  }
  .contact { position: absolute; left: 402px; top: 322px; list-style: none; color: var(--ink); font-size: 23px; }
  .contact li { display: flex; align-items: center; height: 28px; margin-bottom: 13px; }
  .contact li.abn { margin-bottom: 15px; }
  .contact svg { width: 18px; height: 18px; margin-right: 12px; flex: none; }

  .photo {
    position: absolute; inset: 0;
    background: linear-gradient(170deg, #1460c8 0%, #1d7ee6 45%, #2a8ff0 70%, #5d9fdc 100%);
  }
  .back-band { position: absolute; left: 0; right: 0; top: 386px; bottom: 0; background: var(--band); }
  .card--back .wordmark { top: 398px; }
  .card--back .services { top: 487px; color: var(--tag-faint); }
</style>
</head>
<body>

<section class="card card--front">
  <h1 class="wordmark">VARNEX <span class="accent">CONSULTING</span></h1>
  <p class="services">Search &amp; Select<span class="sep">|</span>Career<span class="sep">|</span>Coaching<span class="sep">|</span>Leadership<span class="sep">|</span>Outplacement</p>

  <svg class="front-curve" viewBox="0 0 917 524" aria-hidden="true">
    <path d="M0 339 Q458 131 917 336 L917 524 L0 524 Z" fill="#1e97e6"/>
    <path d="M0 339 Q458 131 917 336" fill="none" stroke="#ffffff" stroke-width="4"/>
  </svg>

  <div class="holder">
    <p class="holder__name">Gavin Threlkeld</p>
    <p class="holder__role">Principal</p>
  </div>
  <div class="divider"></div>

  <ul class="contact">
    <li class="abn">ABN: 71203948865</li>
    <li>
      <svg viewBox="0 0 18 18" aria-hidden="true"><rect width="18" height="18" fill="#0b1520"/><path d="M6 4 L8 4 L8.5 7 L7.3 7.8 Q8.3 10 10.2 10.8 L11 9.6 L14 10 L14 12 Q13.5 14 11.5 13.6 Q5.5 12 4.3 6 Q4 4.3 6 4 Z" fill="#1e97e6"/></svg>
      1300 485 193
    </li>
    <li>
      <svg viewBox="0 0 18 18" aria-hidden="true"><rect width="18" height="18" fill="#0b1520"/><rect x="3.5" y="5" width="11" height="8" fill="none" stroke="#1e97e6" stroke-width="1.3"/><path d="M3.5 5 L9 9.5 L14.5 5" fill="none" stroke="#1e97e6" stroke-width="1.3"/></svg>
      career@varnexconsulting.example
    </li>
    <li>
      <svg viewBox="0 0 18 18" aria-hidden="true"><rect width="18" height="18" fill="#0b1520"/><path d="M9 15 Q4.5 9.5 4.5 7.3 A4.5 4.5 0 0 1 13.5 7.3 Q13.5 9.5 9 15 Z" fill="#1e97e6"/><circle cx="9" cy="7.3" r="1.7" fill="#0b1520"/></svg>
      PO Box 3172&nbsp; Merrowdale NSW 2291
    </li>
  </ul>
</section>

<section class="card card--back">
  <div class="photo" role="img" aria-label="Photograph of a snowboarder mid-jump against a deep blue sky above a snowy mountain peak, with a spray of snow"></div>
  <div class="back-band"></div>
  <h2 class="wordmark">VARNEX <span class="accent">CONSULTING</span></h2>
  <p class="services">Search &amp; Select<span class="sep">|</span>Career<span class="sep">|</span>Coaching<span class="sep">|</span>Leadership<span class="sep">|</span>Outplacement</p>
</section>

</body>
</html>
```